I need a website designed. I am a mortgage loan officer and would like to have a website for me and my team where i can post resources, videos and blog information for my clients. A website like themorvaskteam.com .

The theme is - The Pelkins Team - Home Loan Group powered by Brightwell Home Loans -

Target Market(s)

B2B (Real Estate Agents)and B2C (Home buyers and refinancing)

Industry/Entity Type

Mortgage Lender

Coding

Coded - Design and coding required

Number of Pages Required

5+ page

Font styles to use
Serif
Sans Serif

Colors

Designer to choose colors to be used in the design.

Requirements
Must have
• Disclaimers: Licensed by the Bureau of Lending Affairs under the Pacific Credit Providers Act. Loans made or arranged pursuant to a Pacific Credit Providers Act License. Equal Housing Lender Brightwell Cannot Accept mortgage applications for properties located in New York via this site
• Mobile Friendly
Nice to have
• Main Links: Home, About Us(see team flyer), Mortgage 101, Contact Us (formzig form)

```html
<!DOCTYPE html>
<html lang="en">
<head>
<meta charset="utf-8">
<title>The Pelkins Team – Home Loan Group</title>
<link href="https://fonts.googleapis.com/css2?family=Oswald:wght@400;500;600&family=Open+Sans:wght@400;600;700&display=swap" rel="stylesheet">
<style>
:root{
  --blue:#0b6cc4;
  --blue-dark:#0a4f9e;
  --navy:#1a2a8a;
  --ink:#1c2b4a;
  --text:#555b66;
  --pale:#eaf2fb;
  --footer:#2b2b2b;
  --white:#fff;
  --grey-card:#4a4a4a;
}
*{box-sizing:border-box;margin:0;padding:0}
html,body{width:1200px;height:4337px;overflow:hidden}
body{font-family:"Open Sans",Arial,sans-serif;color:var(--text);background:var(--white);position:relative}
.heading{font-family:"Oswald",Arial,sans-serif;font-weight:500;text-transform:uppercase;color:var(--blue-dark);font-size:34px;text-align:center;letter-spacing:.5px}
.heading::after{content:"";display:block;width:50px;height:3px;background:var(--blue);margin:10px auto 0}

/* header */
.site-header{position:absolute;top:0;left:0;width:1200px;height:130px;background:var(--white);z-index:3}
.brand{position:absolute;left:95px;top:30px;display:flex;align-items:center;gap:12px}
.brand-square{width:22px;height:22px;background:var(--blue-dark)}
.brand-name{font-family:"Oswald",Arial,sans-serif;font-weight:500;color:var(--navy);font-size:30px;line-height:1}
.brand-sub{font-family:"Oswald",Arial,sans-serif;font-weight:500;color:var(--navy);font-size:13px;letter-spacing:4px;margin-top:4px}
.header-band{position:absolute;right:0;top:0;width:700px;height:130px;background:var(--blue);clip-path:polygon(60px 0,100% 0,100% 100%,0 100%)}
.header-band::before{content:"";position:absolute;left:0;top:0;width:120px;height:130px;background:var(--blue-dark);clip-path:polygon(60px 0,100px 0,40px 100%,0 100%)}
.contact-bar{position:absolute;right:95px;top:28px;display:flex;gap:34px;color:var(--white);font-size:17px}
.contact-bar span{display:flex;align-items:center;gap:10px}
.ico{width:30px;height:30px;border-radius:50%;background:var(--white);display:inline-flex;align-items:center;justify-content:center}
.main-nav{position:absolute;right:100px;top:90px;display:flex;gap:52px;font-family:"Oswald",Arial,sans-serif;color:var(--white);font-size:16px}

/* hero */
.hero{position:absolute;top:130px;left:0;width:1200px;height:580px;overflow:hidden}
.hero-photo{position:absolute;inset:0;background:linear-gradient(100deg,#c7d8ea 0%,#e4ecf4 40%,#b8cbe0 70%,#8aa4c4 100%)}
.hero-copy{position:absolute;left:100px;top:95px;color:var(--white)}
.hero-title{font-family:"Oswald",Arial,sans-serif;font-weight:600;font-size:52px;line-height:1}
.hero-sub{font-family:"Oswald",Arial,sans-serif;font-size:36px;margin-top:18px}
.btn{display:inline-block;margin-top:40px;background:var(--blue);color:var(--white);font-family:"Oswald",Arial,sans-serif;font-size:15px;padding:14px 18px}
.arrow{position:absolute;top:200px}
.hero-wave{position:absolute;left:0;bottom:0}

/* profile */
.profile{position:absolute;top:780px;left:0;width:1200px;height:480px}
.profile-photo{position:absolute;left:100px;top:30px;width:305px;height:420px;border:5px solid var(--navy);border-radius:12px;background:linear-gradient(180deg,#e9edf2,#b7bec8)}
.profile-body{position:absolute;left:455px;top:50px;width:645px}
.profile-name{font-family:"Oswald",Arial,sans-serif;font-weight:500;color:var(--blue-dark);font-size:34px}
.profile-role{font-size:21px;color:var(--ink);margin-top:8px}
.profile-bio{font-size:14.5px;line-height:1.75;margin-top:22px}
.profile-contact{display:grid;grid-template-columns:400px 245px;gap:18px 0;margin-top:26px;font-size:17px;color:var(--ink)}
.profile-contact span{display:flex;align-items:center;gap:12px}
.ico-line{width:32px;height:32px;border-radius:50%;border:2px solid var(--blue);display:inline-flex;align-items:center;justify-content:center;flex:none}

/* videos */
.videos{position:absolute;top:1325px;left:0;width:1200px;height:495px;background:var(--pale);padding-top:62px}
.card-row{display:flex;gap:40px;position:absolute;left:100px;top:170px}
.media{width:313px}
.media-photo{height:215px;border-radius:12px;position:relative;display:flex;align-items:center;justify-content:center}
.media-caption{font-size:19px;font-weight:600;color:var(--blue);text-align:center;margin-top:24px}
.media-text{font-size:14px;line-height:1.6;text-align:center;margin-top:10px}

/* resources */
.resources{position:absolute;top:1820px;left:0;width:1200px;height:498px;background:linear-gradient(90deg,#1262b7,#1c7bd0 50%,#1262b7);color:var(--white);text-align:center;padding-top:78px}
.resources .heading{color:var(--white)}
.resources .heading::after{background:var(--white)}
.res-icon{margin:55px auto 0;display:block}
.res-title{font-family:"Open Sans",Arial,sans-serif;font-weight:600;font-size:25px;margin-top:40px}
.res-text{font-size:14.5px;line-height:1.8;width:1080px;margin:20px auto 0}

/* team */
.team{position:absolute;top:2318px;left:0;width:1200px;height:717px;padding-top:85px}
.team-row{position:absolute;left:100px;top:170px;display:flex;gap:45px}
.member{width:305px;height:375px;border-radius:18px;background:var(--blue);color:var(--white);text-align:center;position:relative;padding:95px 22px 0;margin-top:70px}
.member.alt{background:var(--grey-card)}
.member-photo{position:absolute;left:50%;top:-70px;transform:translateX(-50%);width:150px;height:150px;border-radius:50%;border:5px solid var(--white);background:linear-gradient(180deg,#d6dbe2,#8c96a4)}
.member-name{font-family:"Oswald",Arial,sans-serif;font-weight:500;font-size:25px;line-height:1.3}
.member-meta{font-size:12px;font-weight:700;line-height:1.5;margin-top:6px;overflow-wrap:anywhere}
.member-text{font-size:13.5px;line-height:1.55;margin-top:16px}

/* blog */
.blog{position:absolute;top:3035px;left:0;width:1200px;height:600px;background:var(--pale);padding-top:88px}
.blog .card-row{top:185px}

/* footer */
.footer{position:absolute;top:3615px;left:0;width:1200px;height:722px;background:var(--footer);color:var(--white)}
.footer-wave{position:absolute;top:-60px;left:0}
.footer-brand{position:absolute;left:100px;top:310px;display:flex;align-items:center;gap:14px;font-family:"Oswald",Arial,sans-serif;font-size:28px;line-height:1.15}
.footer-brand i{width:28px;height:28px;background:var(--white);display:block;flex:none}
.footer-contact{position:absolute;left:470px;top:300px;font-family:"Oswald",Arial,sans-serif;font-size:22px;line-height:1.35}
.footer-contact div{display:flex;gap:16px;margin-bottom:20px;align-items:flex-start}
.footer-social{position:absolute;left:935px;top:300px;font-family:"Oswald",Arial,sans-serif;font-size:22px}
.footer-social div{display:flex;gap:16px;align-items:center;margin-bottom:26px}
.ring{width:36px;height:36px;border-radius:50%;border:2px solid var(--white);display:inline-flex;align-items:center;justify-content:center;flex:none}
.disclaimer{position:absolute;left:95px;top:578px;width:1010px;font-size:14px;font-weight:700;line-height:2;text-align:center}
.copyright{position:absolute;top:668px;width:1200px;text-align:center;font-size:14px;font-weight:700}
</style>
</head>
<body>

<header class="site-header">
  <div class="brand">
    <span class="brand-square"></span>
    <div><div class="brand-name">THE PELKINS TEAM</div><div class="brand-sub">HOME LOAN GROUP</div></div>
  </div>
  <div class="header-band"></div>
  <div class="contact-bar">
    <span><i class="ico"><svg width="16" height="12" viewBox="0 0 16 12"><rect x="1" y="1" width="14" height="10" fill="none" stroke="#0b6cc4" stroke-width="2"/><path d="M1 1l7 6 7-6" fill="none" stroke="#0b6cc4" stroke-width="2"/></svg></i>info@thepelkinsteam.com</span>
    <span><i class="ico"><svg width="14" height="14" viewBox="0 0 14 14"><path d="M3 1l3 3-2 2c1 2 2 3 4 4l2-2 3 3-2 2C6 13 1 8 1 3z" fill="#0b6cc4"/></svg></i>1-555-014-7202</span>
  </div>
  <nav class="main-nav"><span>HOME</span><span>ABOUT US</span><span>MORTGAGE 101</span><span>CONTACT US</span></nav>
</header>

<section class="hero">
  <div class="hero-photo" role="img" aria-label="Loan officer in shirt and tie reviewing documents in a bright office"></div>
  <svg class="arrow" style="left:28px" width="30" height="60" viewBox="0 0 30 60"><path d="M24 4L6 30l18 26" fill="none" stroke="#fff" stroke-width="3"/></svg>
  <svg class="arrow" style="right:28px" width="30" height="60" viewBox="0 0 30 60"><path d="M6 4l18 26L6 56" fill="none" stroke="#fff" stroke-width="3"/></svg>
  <div class="hero-copy">
    <div class="hero-title">THE PELKINS TEAM</div>
    <div class="hero-sub">HOME LOAN GROUP</div>
    <span class="btn">READ MORE</span>
  </div>
  <svg class="hero-wave" width="1200" height="160" viewBox="0 0 1200 160" preserveAspectRatio="none">
    <path d="M0 40 C250 120 600 150 900 80 C1020 50 1120 30 1200 40 L1200 160 L0 160Z" fill="#1a2a8a"/>
    <path d="M0 70 C260 145 620 150 900 100 C1030 78 1130 70 1200 80 L1200 160 L0 160Z" fill="#0b6cc4"/>
    <path d="M0 105 C300 165 650 150 920 115 C1050 100 1140 110 1200 120 L1200 160 L0 160Z" fill="#fff"/>
  </svg>
</section>

<section class="profile">
  <div class="profile-photo" role="img" aria-label="Portrait of the producing branch manager"></div>
  <div class="profile-body">
    <h1 class="profile-name">MARCO PELKINS</h1>
    <div class="profile-role">Producing Branch Manager</div>
    <p class="profile-bio">I have over 15 years of experience in Mortgage Planning. I rank in the top 1% of loan originators in the country. I pride myself on making the home buying process as smooth as possible. I will guide you through the mortgage process and look forward to helping you with your transaction. My team has been awarded with the Circle of Excellence award and CEO Club for being in the top 5 teams in the country having helped over 700+ families achieve the dream of home ownership between the years 2016 and 2017 and counting.</p>
    <div class="profile-contact">
      <span><i class="ico-line"><svg width="14" height="10" viewBox="0 0 16 12"><rect x="1" y="1" width="14" height="10" fill="none" stroke="#0b6cc4" stroke-width="2"/><path d="M1 1l7 6 7-6" fill="none" stroke="#0b6cc4" stroke-width="2"/></svg></i>marco.pelkins@brightwellhomeloans.com</span>
      <span><i class="ico-line"><svg width="13" height="13" viewBox="0 0 14 14"><path d="M3 1l3 3-2 2c1 2 2 3 4 4l2-2 3 3-2 2C6 13 1 8 1 3z" fill="#0b6cc4"/></svg></i>Office: (555) 014-5050</span>
      <span><i class="ico-line"><svg width="12" height="15" viewBox="0 0 12 16"><path d="M6 15C2 10 1 8 1 6a5 5 0 0110 0c0 2-1 4-5 9z" fill="#0b6cc4"/><circle cx="6" cy="6" r="2" fill="#fff"/></svg></i>Brightwell Home Loans, Inc – NMLS 40817</span>
      <span><i class="ico-line"><svg width="13" height="13" viewBox="0 0 14 14"><path d="M3 1l3 3-2 2c1 2 2 3 4 4l2-2 3 3-2 2C6 13 1 8 1 3z" fill="#0b6cc4"/></svg></i>Fax: (555) 014-8232</span>
    </div>
  </div>
</section>

<section class="videos">
  <h2 class="heading">OUR VIDEOS</h2>
  <div class="card-row">
    <div class="media"><div class="media-photo" role="img" aria-label="Video still: calculator and house model on a desk" style="background:linear-gradient(135deg,#8c7a66,#c9b59c)"><svg width="70" height="70" viewBox="0 0 70 70"><circle cx="35" cy="35" r="32" fill="none" stroke="#fff" stroke-width="4"/><path d="M28 22l20 13-20 13z" fill="#fff"/></svg></div><div class="media-caption">Nemo enim ipsam voluptatem</div></div>
    <div class="media"><div class="media-photo" role="img" aria-label="Video still: couple meeting with an advisor" style="background:linear-gradient(135deg,#a88d73,#e2d2c0)"><svg width="70" height="70" viewBox="0 0 70 70"><circle cx="35" cy="35" r="32" fill="none" stroke="#fff" stroke-width="4"/><path d="M28 22l20 13-20 13z" fill="#fff"/></svg></div><div class="media-caption">Nemo enim ipsam voluptatem</div></div>
    <div class="media"><div class="media-photo" role="img" aria-label="Video still: hands handing over house keys" style="background:linear-gradient(135deg,#7b6a5a,#c2ad97)"><svg width="70" height="70" viewBox="0 0 70 70"><circle cx="35" cy="35" r="32" fill="none" stroke="#fff" stroke-width="4"/><path d="M28 22l20 13-20 13z" fill="#fff"/></svg></div><div class="media-caption">Nemo enim ipsam voluptatem</div></div>
  </div>
</section>

<section class="resources">
  <h2 class="heading">OUR RESOURCES</h2>
  <svg class="res-icon" width="100" height="100" viewBox="0 0 100 100"><path d="M10 48L50 12l40 36" fill="none" stroke="#fff" stroke-width="7" stroke-linejoin="round"/><path d="M22 42v46h56V42" fill="none" stroke="#fff" stroke-width="7"/><circle cx="62" cy="68" r="18" fill="#fff"/><text x="62" y="76" text-anchor="middle" font-family="Oswald,Arial,sans-serif" font-size="22" font-weight="600" fill="#0b6cc4">$</text></svg>
  <div class="res-title">MORTGAGE LOAN OFFICER</div>
  <p class="res-text">Sed ut perspiciatis unde omnis iste natus error sit voluptatem accusantium doloremque laudantium, totam rem aperiam, eaque ipsa quae ab illo inventore veritatis et quasi architecto beatae vitae dicta sunt explicabo.</p>
</section>

<section class="team">
  <h2 class="heading">OUR TEAM</h2>
  <div class="team-row">
    <div class="member"><div class="member-photo" role="img" aria-label="Portrait of loan partner"></div><div class="member-name">TOMAS REYVAR</div><div class="member-meta">Loan Partner I - NMLS ID 2091735<br>Tomas.Reyvar@brightwellhomeloans.com<br>(555) 014-7202</div><p class="member-text">I am able to help customers with pre-qualifications and pre-approvals and keep the applicants and real estate agents informed during the application process.</p></div>
    <div class="member alt"><div class="member-photo" role="img" aria-label="Portrait of loan processor"></div><div class="member-name">LUIS DANFORTH</div><div class="member-meta">Loan Processor - NMLS ID: 2093318<br>Luis.Danforth@brightwellhomeloans.com<br>(555) 014-9294</div><p class="member-text">I verify loan documents including income, credit, appraisal and title insurance, preparing the loan application for submittal to underwriting.</p></div>
    <div class="member"><div class="member-photo" role="img" aria-label="Portrait of closing coordinator"></div><div class="member-name">NORA VELLACOTT</div><div class="member-meta">Closing Coordinator/Team Leader-NMLS 2095604<br>Nora.Vellacott@brightwellhomeloans.com<br>(555) 014-1151</div><p class="member-text">I guide our clients with any conditions or stipulations set by underwriting post loan conditional approval. I make sure all the transaction deadlines.</p></div>
  </div>
</section>

<section class="blog">
  <h2 class="heading">OUR BLOG</h2>
  <div class="card-row">
    <div class="media"><div class="media-photo" role="img" aria-label="Blog photo: hands using a calculator over paperwork" style="background:linear-gradient(135deg,#5d6670,#c5ccd4)"></div><div class="media-caption">Nemo enim ipsam voluptatem</div><p class="media-text">Sed ut perspiciatis unde omnis iste natus error sit voluptatem accusantium doloremque laudantium.</p></div>
    <div class="media"><div class="media-photo" role="img" aria-label="Blog photo: smiling client in a meeting" style="background:linear-gradient(135deg,#7a6a60,#d9cfc6)"></div><div class="media-caption">Nemo enim ipsam voluptatem</div><p class="media-text">Sed ut perspiciatis unde omnis iste natus error sit voluptatem accusantium doloremque laudantium.</p></div>
    <div class="media"><div class="media-photo" role="img" aria-label="Blog photo: team discussing at a table" style="background:linear-gradient(135deg,#8a8f96,#e1e4e8)"></div><div class="media-caption">Nemo enim ipsam voluptatem</div><p class="media-text">Sed ut perspiciatis unde omnis iste natus error sit voluptatem accusantium doloremque laudantium.</p></div>
  </div>
</section>

<footer class="footer">
  <svg class="footer-wave" width="1200" height="260" viewBox="0 0 1200 260" preserveAspectRatio="none">
    <path d="M0 0 C300 110 650 120 900 80 C1040 58 1130 40 1200 30 L1200 0Z" fill="#eaf2fb"/>
    <path d="M0 0 C300 110 650 120 900 80 C1040 58 1130 40 1200 30 L1200 150 C1000 100 700 200 400 170 C220 150 90 90 0 60Z" fill="#1a2a8a"/>
    <path d="M0 60 C90 90 220 150 400 170 C700 200 1000 100 1200 150 L1200 200 C1000 150 700 250 400 220 C220 200 90 150 0 120Z" fill="#0b6cc4"/>
    <path d="M0 120 C90 150 220 200 400 220 C700 250 1000 150 1200 200 L1200 260 L0 260Z" fill="#2b2b2b"/>
  </svg>
  <div class="footer-brand"><i></i><span>BRIGHTWELL<br>HOME LOANS</span></div>
  <div class="footer-contact">
    <div><span class="ring"><svg width="14" height="14" viewBox="0 0 14 14"><path d="M3 1l3 3-2 2c1 2 2 3 4 4l2-2 3 3-2 2C6 13 1 8 1 3z" fill="#fff"/></svg></span>1-555-014-7202</div>
    <div><span class="ring"><svg width="12" height="15" viewBox="0 0 12 16"><path d="M6 15C2 10 1 8 1 6a5 5 0 0110 0c0 2-1 4-5 9z" fill="#fff"/><circle cx="6" cy="6" r="2" fill="#2b2b2b"/></svg></span>4120 LINDENFIELD RD, SUITE 209,<br>MARLOW FL 30418</div>
  </div>
  <div class="footer-social">
    <div><span class="ring"></span>FRIENDLINE</div>
    <div><span class="ring"></span>SHORTPOST</div>
    <div><span class="ring"></span>CIRCLEUP</div>
  </div>
  <p class="disclaimer">Licensed by the Bureau of Lending Affairs under the Pacific Credit Providers Act. Loans made or arranged pursuant to a Pacific Credit Providers Act License. Equal Housing Lender Brightwell Cannot Accept mortgage applications for properties located in New York via this site.</p>
  <div class="copyright">Copyrights @ 2018 The Pelkins Team. All Rights Reserved.</div>
</footer>

</body>
</html>
```